I need a business card to give to prospective clients. I am a freelance photographer who photographs most things (except weddings and social stuff) including nature, wildlife and interiors.
I want to look modern and stylish.
I am including a photograph although I am by no means certain that it should be used - what do you think?
More of my images can be seen and downloaded at my PixVault page - just search for Maren Tolbeck
Target Market(s)
Home owners selling or letting properties, private individuals wanting to buy prints
Industry/Entity Type
Business
Contact Information for Business Card
Maren Tolbeck Photography
Maren
Wrenfield Cottage, Mossbank Road, Pelsworth, Carrow Heath, KX41 2RB
Tel: +44 7000 418263. Email: maren@tolbeckstudio.example

```html
<!DOCTYPE html>
<html lang="en">
<head>
<meta charset="utf-8">
<title>Maren Tolbeck Photography – Business Card</title>
<link rel="stylesheet" href="https://fonts.googleapis.com/css2?family=Libre+Baskerville:wght@400;700&family=Quicksand:wght@400;500&display=swap">
<style>
  :root {
    --ink: #111111;
    --paper: #ffffff;
    --stage: #ece9e5;
    --copper: #c47c4a;
    --copper-soft: #a8673c;
    --navy-deep: #2a283f;
    --navy-mid: #3b3957;
    --navy-light: #5a5778;
    --card-text: #f4f1ee;
  }
  * { margin: 0; padding: 0; box-sizing: border-box; }
  html, body { width: 1200px; height: 1000px; overflow: hidden; }
  body { background: var(--paper); font-family: "Libre Baskerville", Georgia, serif; position: relative; }

  .brand-header {
    position: absolute; top: 0; left: 0; width: 1200px; height: 250px;
    background: var(--paper);
    display: flex; flex-direction: column; align-items: center; justify-content: center;
  }
  .brand-ring {
    width: 96px; height: 96px; border-radius: 50%;
    border: 3px solid var(--ink); margin-bottom: 16px;
  }
  .brand-name {
    font-family: "Libre Baskerville", Georgia, serif; font-weight: 700;
    font-size: 36px; letter-spacing: 0.5px; color: var(--ink); line-height: 1;
  }
  .brand-tagline {
    font-family: "Quicksand", Arial, sans-serif; font-size: 17px;
    letter-spacing: 6px; color: var(--ink); margin-top: 6px;
  }

  .card-stage {
    position: absolute; top: 250px; left: 0; width: 1200px; height: 750px;
    background: var(--stage);
  }
  .card {
    position: absolute; top: 220px; width: 540px; height: 309px;
    border-radius: 3px; overflow: hidden;
    box-shadow: 0 10px 28px rgba(0,0,0,0.22);
  }
  .card--back { left: 40px; }
  .card--front {
    left: 620px;
    background: linear-gradient(100deg, var(--navy-deep) 0%, var(--navy-mid) 55%, var(--navy-light) 100%);
    display: flex; flex-direction: column; align-items: center; justify-content: center;
  }

  .card-photo {
    position: absolute; inset: 0;
    background:
      linear-gradient(180deg, rgba(0,0,0,0) 70%, rgba(40,34,30,0.55) 100%),
      radial-gradient(ellipse at 62% 58%, #b9785a 0%, #7c5a6e 22%, rgba(60,58,90,0) 55%),
      linear-gradient(180deg, #3c3a5a 0%, #4c4a6c 45%, #6b5a66 68%, #6d6248 78%, #4a4032 100%);
  }
  .card-info {
    position: absolute; left: 34px; top: 34px; color: var(--card-text);
  }
  .card-ring--small {
    width: 54px; height: 54px; border-radius: 50%;
    border: 2px solid var(--copper); margin: 0 0 8px 40px;
  }
  .card-name--small {
    font-weight: 700; font-size: 17px; color: var(--copper); letter-spacing: 0.4px; line-height: 1;
  }
  .card-tagline--small {
    font-family: "Quicksand", Arial, sans-serif; font-size: 9px; letter-spacing: 4px;
    color: var(--copper); margin: 3px 0 0 44px;
  }
  .card-address {
    font-style: normal; font-size: 11px; line-height: 14px; margin-top: 22px;
  }
  .card-contact { margin-top: 14px; font-size: 11px; line-height: 16px; }
  .card-contact .contact-email { font-family: "Quicksand", Arial, sans-serif; font-size: 11px; }

  .card-ring {
    width: 104px; height: 104px; border-radius: 50%;
    border: 3px solid var(--copper); margin-bottom: 16px;
  }
  .card-name {
    font-weight: 700; font-size: 30px; color: var(--copper); letter-spacing: 0.5px; line-height: 1;
  }
  .card-tagline {
    font-family: "Quicksand", Arial, sans-serif; font-size: 15px; letter-spacing: 6px;
    color: var(--copper); margin-top: 5px;
  }
</style>
</head>
<body>
  <header class="brand-header">
    <div class="brand-ring"></div>
    <div class="brand-name">MAREN TOLBECK</div>
    <div class="brand-tagline">photography</div>
  </header>

  <main class="card-stage">
    <section class="card card--back">
      <div class="card-photo" role="img" aria-label="Dusk savanna photograph with a herd of elephants under a purple and amber sky"></div>
      <div class="card-info">
        <div class="card-ring--small"></div>
        <div class="card-name--small">MAREN TOLBECK</div>
        <div class="card-tagline--small">photography</div>
        <address class="card-address">
          Wrenfield Cottage<br>
          Mossbank Road<br>
          Pelsworth<br>
          Carrow Heath, KX41 2RB
        </address>
        <div class="card-contact">
          <div>Tel: +44 7000 418263</div>
          <div class="contact-email">Email: maren@tolbeckstudio.example</div>
        </div>
      </div>
    </section>

    <section class="card card--front">
      <div class="card-ring"></div>
      <div class="card-name">MAREN TOLBECK</div>
      <div class="card-tagline">photography</div>
    </section>
  </main>
</body>
</html>
```